Fresh, modern, fun business card for pediatric dental practice

Need a business card for fresh, modern, fun pediatric dental practice

Clean look that matches our website's font and colors

We prefer the look of curved corners on business cards

Target Market(s)

parents (mothers) of young children, professionals, mid-high class

Industry/Entity Type

Dental

Contact Information for Business Card

Maplebrook Pediatric Dentistry
482 Quarry Lane
Suite 517
Lititz, PA 17543
717.555.0193
www.maplebrookkidsdental.example

Mei-Ran Tsai, DMD
Corinne Walbeck, DMD
(we are working on our email address, but we would like that on the card as well)

Font styles to use
Sans Serif

Requirements
Must have
• All info; we would also like to make cards for individual staff members
• colors from our website and color palatte, attatched
• use same font and design as website for branding
Nice to have
• clean, simple card that has a pop of color
• we would like to see a few designs with our tag line "where smiles get brighter"
• we are not sure if we want to have it on there or not
• we would like to see a few designs incorporating the ribbon graphic on our website where the word WELCOME is

```html
<!DOCTYPE html>
<html lang="en">
<head>
<meta charset="utf-8">
<title>Maplebrook Pediatric Dentistry – Business Cards</title>
<link rel="stylesheet" href="https://fonts.googleapis.com/css2?family=Open+Sans:wght@400;600&display=swap">
<style>
  :root {
    --backdrop: #ece8e3;
    --kraft-light: #d2b386;
    --kraft: #c6a571;
    --kraft-dark: #b8955f;
    --ink: #141210;
    --rule: #3a3127;
  }
  * { box-sizing: border-box; margin: 0; padding: 0; }
  html, body {
    width: 1200px; height: 900px; overflow: hidden;
    background: var(--backdrop);
    font-family: "Open Sans", sans-serif;
    color: var(--ink);
  }
  .canvas { position: relative; width: 1200px; height: 900px; }

  .card {
    position: absolute;
    border-radius: 6px;
    background: linear-gradient(160deg, var(--kraft-light) 0%, var(--kraft) 55%, var(--kraft-dark) 100%);
    box-shadow: 0 10px 28px rgba(0,0,0,0.18);
    overflow: hidden;
  }

  /* Contact side */
  .card--contact { left: 238px; top: 60px; width: 555px; height: 345px; }
  .brand-block {
    position: absolute; left: 34px; top: 0; width: 200px; height: 100%;
    display: flex; flex-direction: column; align-items: center; justify-content: center; gap: 14px;
    text-align: center;
  }
  .brand-dot { width: 70px; height: 70px; border-radius: 50%; background: var(--ink); }
  .brand-block__name { font-size: 17px; font-weight: 600; line-height: 1.25; }
  .divider {
    position: absolute; left: 255px; top: 64px; width: 1px; height: 218px; background: var(--rule);
  }
  .details { position: absolute; left: 278px; top: 68px; width: 262px; }
  .person__name { font-size: 17px; font-weight: 600; line-height: 22px; }
  .person__email { font-size: 12.5px; line-height: 18px; margin-bottom: 6px; }
  .contact-list { list-style: none; margin-top: 12px; }
  .contact-list li {
    display: flex; align-items: flex-start; gap: 7px;
    font-size: 13px; line-height: 19px; margin-bottom: 2px;
  }
  .contact-list svg { width: 13px; height: 13px; flex: none; margin-top: 3px; }

  /* Brand side */
  .card--brand { left: 458px; top: 518px; width: 560px; height: 345px; }
  .brand-face {
    position: absolute; inset: 0;
    display: flex; flex-direction: column; align-items: center; justify-content: center; gap: 18px;
    text-align: center;
  }
  .brand-face .brand-dot { width: 84px; height: 84px; }
  .brand-face__name { font-size: 40px; font-weight: 600; line-height: 1.1; }
</style>
</head>
<body>
<main class="canvas">

  <section class="card card--contact" aria-label="Business card, contact side">
    <div class="brand-block">
      <span class="brand-dot" aria-hidden="true"></span>
      <p class="brand-block__name">Maplebrook<br>Pediatric Dentistry</p>
    </div>
    <div class="divider" aria-hidden="true"></div>
    <div class="details">
      <div class="person">
        <p class="person__name">Mei-Ran Tsai, DMD</p>
        <p class="person__email">mei-ran@maplebrookkidsdental.example</p>
      </div>
      <div class="person">
        <p class="person__name">Corinne Walbeck, DMD</p>
        <p class="person__email">corinne@maplebrookkidsdental.example</p>
      </div>
      <ul class="contact-list">
        <li>
          <svg viewBox="0 0 12 16" aria-hidden="true"><path d="M6 .8a4.9 4.9 0 0 0-4.9 4.9C1.1 9.5 6 15.2 6 15.2s4.9-5.7 4.9-9.5A4.9 4.9 0 0 0 6 .8z" fill="#141210"/><circle cx="6" cy="5.7" r="1.8" fill="#c6a571"/></svg>
          <span>482 Quarry Lane, Suite 517<br>Lititz, PA 17543</span>
        </li>
        <li>
          <svg viewBox="0 0 12 16" aria-hidden="true"><rect x="1.5" y="0.8" width="9" height="14.4" rx="1.6" fill="none" stroke="#141210" stroke-width="1.6"/><circle cx="6" cy="12.6" r="0.9" fill="#141210"/></svg>
          <span>717.555.0193</span>
        </li>
        <li>
          <svg viewBox="0 0 16 16" aria-hidden="true"><circle cx="8" cy="8" r="7.5" fill="#141210"/><path d="M1 8h14M8 .5c-3 3.5-3 11.5 0 15M8 .5c3 3.5 3 11.5 0 15" fill="none" stroke="#c6a571" stroke-width="1"/></svg>
          <span>www.maplebrookkidsdental.example</span>
        </li>
      </ul>
    </div>
  </section>

  <section class="card card--brand" aria-label="Business card, brand side">
    <div class="brand-face">
      <span class="brand-dot" aria-hidden="true"></span>
      <p class="brand-face__name">Maplebrook<br>Pediatric Dentistry</p>
    </div>
  </section>

</main>
</body>
</html>
```